We need a cover designed for our book on parenting. The focus of this book is on the parents, not on the child! We like the idea of this title having a double meaning - insight as in gaining insights into parenting, and "in sight" as in looking inward as parents and how to improve ourselves rather than looking outward to improve our children. We would love for the cover to somehow represent this double meaning. I can upload an excerpt from the book soon over the next few days.

Reason: We are still reviewing the amazing designs! Thank you so much! :)

Target Market(s)

Parents with kids of any age from babies through adult children.

Requirements
Must have
• Title is: Harborlight Parenting
• Subtitle is: Steady Homes, Calmer Hearts Ahead
• Authors names: Lena Marsh, LCSW Oscar Marsh, Ph.D.

```html
<!DOCTYPE html>
<html lang="en">
<head>
<meta charset="utf-8">
<title>Harborlight Parenting – Cover</title>
<link rel="stylesheet" href="https://fonts.googleapis.com/css2?family=Oswald:wght@700&family=Ubuntu:wght@500;700&family=Open+Sans:wght@400&display=swap">
<style>
  :root {
    --stage: #eeeeee;
    --sky-top: #1b4a80;
    --sky-mid: #3d6f9c;
    --dusk: #c99a5c;
    --sun: #fff3cf;
    --ground: #140d12;
    --title: #f4f4f2;
    --accent: #f5d20a;
    --body-text: #eef1f5;
  }
  * { box-sizing: border-box; margin: 0; padding: 0; }
  html, body { width: 1200px; height: 1200px; overflow: hidden; }
  body {
    background: var(--stage);
    display: flex;
    align-items: center;
    justify-content: center;
    gap: 60px;
  }
  .cover {
    position: relative;
    width: 480px;
    height: 720px;
    overflow: hidden;
    box-shadow: 0 12px 30px rgba(0,0,0,0.25);
  }
  .cover-art {
    position: absolute;
    inset: 0;
    background:
      radial-gradient(ellipse 38% 14% at 56% 66%, var(--sun) 0%, rgba(255,214,140,0.75) 35%, rgba(230,150,60,0) 100%),
      linear-gradient(to bottom, var(--sky-top) 0%, var(--sky-mid) 35%, var(--dusk) 58%, #d98a3a 66%, var(--ground) 72%, var(--ground) 100%);
  }
  .cover-back .cover-art {
    background:
      linear-gradient(to bottom, #18356e 0%, #2a4f86 35%, #7f7a72 56%, var(--ground) 62%, var(--ground) 100%);
  }
  .authors {
    position: absolute;
    top: 78px;
    left: 0; right: 0;
    text-align: center;
    font-family: "Ubuntu", sans-serif;
    font-weight: 500;
    font-size: 22px;
    color: var(--title);
  }
  .title {
    position: absolute;
    top: 130px;
    left: 0; right: 0;
    text-align: center;
    font-family: "Oswald", sans-serif;
    font-weight: 700;
    font-size: 80px;
    line-height: 1.02;
    letter-spacing: -1px;
    color: var(--title);
    text-transform: uppercase;
  }
  .subtitle {
    position: absolute;
    left: 0; right: 0;
    text-align: center;
    font-family: "Ubuntu", sans-serif;
    font-weight: 700;
    color: var(--accent);
    line-height: 1.2;
  }
  .cover-front .subtitle { bottom: 100px; font-size: 34px; }
  .cover-back .subtitle { top: 90px; font-size: 36px; }
  .blurb {
    position: absolute;
    top: 200px;
    left: 44px; right: 44px;
    text-align: center;
    font-family: "Open Sans", sans-serif;
    font-size: 17px;
    line-height: 1.6;
    color: var(--body-text);
  }
</style>
</head>
<body>
  <section class="cover cover-front">
    <div class="cover-art" role="img" aria-label="Sunset photograph over a dark hill with a lone tree silhouette and two small figures doing handstands against the glowing sun"></div>
    <p class="authors">Lena Marsh, LCSW &amp; Oscar Marsh, Ph.D</p>
    <h1 class="title">Harborlight<br>Parenting</h1>
    <p class="subtitle">Steady Homes,<br>Calmer Hearts Ahead</p>
  </section>

  <section class="cover cover-back">
    <div class="cover-art" role="img" aria-label="Twilight starry sky over a dark hillside with a lone tree silhouette"></div>
    <h2 class="subtitle">Steady Homes,<br>Calmer Hearts Ahead</h2>
    <p class="blurb">We need a cover designed for our book on parenting. The focus of this book is on the parents, not on the child! We like the idea of this title having a double meaning - insight as in gaining insights into parenting, and "in sight" as in looking inward as parents and how to improve ourselves rather than looking outward to improve our children. We would love for the cover to somehow represent this double meaning. I can upload an excerpt from the book soon over the next few days.</p>
  </section>
</body>
</html>
```